Tech business card design

We need an amazing business card design for our new business 'Pexla' a marketing tech startup based in Sydney, Australia. We provide an online marketplace for businesses to search and buy advertising media, connect with service providers and learn more about marketing. We wish to communicate 'cool tech', reliability and professionalism and design based around our logo.

Target Market(s)

Business Owners

Contact Information for Business Card

Name
Position
Email Address
Website
Phone Number

Font styles to use
Other font styles liked:
• Avenir & Avenir Next

Colors

Designer to choose colors to be used in the design.

```html
<!DOCTYPE html>
<html lang="en">
<head>
<meta charset="utf-8">
<title>Pexla Business Card</title>
<link rel="stylesheet" href="https://fonts.googleapis.com/css2?family=Nunito+Sans:wght@400;600;800&display=swap">
<style>
  :root {
    --backdrop: #3a3a3c;
    --navy: #0e0f3a;
    --navy-deep: #07081f;
    --indigo-glow: #2a2f9a;
    --accent: #b9c4ff;
    --white: #ffffff;
    --muted: #d9dcf2;
  }
  * { box-sizing: border-box; margin: 0; padding: 0; }
  html, body {
    width: 1200px; height: 1000px; overflow: hidden;
    background: var(--backdrop);
    font-family: "Nunito Sans", "Avenir Next", Avenir, sans-serif;
  }
  .stage {
    position: relative; width: 1200px; height: 1000px;
    display: flex; flex-direction: column; align-items: center; justify-content: center; gap: 44px;
  }
  .card {
    position: relative; width: 770px; height: 440px;
    border-radius: 30px; overflow: hidden;
    box-shadow: 0 18px 40px rgba(0,0,0,.45);
  }
  .card-front { background: var(--navy-deep); }
  .front-artwork {
    position: absolute; inset: 0;
    background: radial-gradient(ellipse at 62% 48%, var(--indigo-glow) 0%, #14164f 35%, var(--navy-deep) 80%);
  }
  .wordmark {
    position: absolute; color: var(--white);
    font-weight: 800; letter-spacing: -2px; line-height: 1;
  }
  .card-front .wordmark { font-size: 150px; left: 50%; top: 50%; transform: translate(-50%, -55%); }
  .tm { font-size: 16px; font-weight: 800; letter-spacing: 0; margin-left: 6px; vertical-align: bottom; }
  .card-back { background: var(--navy); }
  .identity { position: absolute; left: 0; top: 44px; display: flex; gap: 24px; }
  .identity-marker { width: 18px; height: 46px; background: var(--accent); }
  .person-name { color: var(--white); font-size: 26px; font-weight: 400; line-height: 1.1; }
  .person-role { color: var(--muted); font-size: 15px; margin-top: 2px; }
  .contact-list { position: absolute; left: 44px; bottom: 52px; list-style: none; }
  .contact-item { display: flex; align-items: center; gap: 14px; color: var(--white); font-size: 22px; line-height: 32px; }
  .contact-icon { width: 18px; height: 18px; flex: none; }
  .card-back .wordmark { font-size: 132px; right: 50px; bottom: 44px; }
</style>
</head>
<body>
<main class="stage">
  <section class="card card-front">
    <div class="front-artwork" role="img" aria-label="Dark blue abstract circuit and data-line technology texture"></div>
    <div class="wordmark">pexla<span class="tm">TM</span></div>
  </section>

  <section class="card card-back">
    <div class="identity">
      <div class="identity-marker"></div>
      <div>
        <p class="person-name">Marcus Lane</p>
        <p class="person-role">Managing Director</p>
      </div>
    </div>
    <ul class="contact-list">
      <li class="contact-item">
        <svg class="contact-icon" viewBox="0 0 24 24" fill="none" stroke="#fff" stroke-width="2" stroke-linejoin="round"><path d="M5 3h4l2 5-2.5 1.5a11 11 0 0 0 6 6L16 13l5 2v4a2 2 0 0 1-2 2A16 16 0 0 1 3 5a2 2 0 0 1 2-2z"/></svg>
        800-214-0531
      </li>
      <li class="contact-item">
        <svg class="contact-icon" viewBox="0 0 24 24" fill="none" stroke="#fff" stroke-width="2"><rect x="3" y="5" width="18" height="14" rx="1"/><path d="M3 6l9 7 9-7"/></svg>
        marcusl@pexlamail.com
      </li>
      <li class="contact-item">
        <svg class="contact-icon" viewBox="0 0 24 24" fill="none" stroke="#fff" stroke-width="2"><circle cx="12" cy="12" r="9"/><path d="M3 12h18M12 3c3 3 3 15 0 18M12 3c-3 3-3 15 0 18"/></svg>
        www.pexla.com
      </li>
    </ul>
    <div class="wordmark">pexla<span class="tm">TM</span></div>
  </section>
</main>
</body>
</html>
```